Business card for marketing analytics company

Need a business card for new company. I have a logo already that I want to be built into the card and should use those colours

Company is called steered by tallies
Design must bring steered by tallies to life not be a card that could be for anyone with a logo put on it.

Like the front to be fairly clean and uncluttered bringing the logo out with a suitable design on the back of the card.

The logo represents a compass and business growth so those themes along with numbers, analytics , data are appropriate.
I'm often working with creative industries so also needs to reflect the creative side of analytics rather than be very corporate looking.

Target Market(s)

Ad agency, media agency, consumer goods clients

Industry/Entity Type

Market Research

Contact Information for Business Card

Needs to include name, title, email and phone number

Colors
f78f20
f68d4d
ec1f27

Requirements
Must have
• Must bring steered by tallies to life not be a card that could be for anyone with a logo put on it.
• Logo, Correct colours
• Like a design on the back that relates to company name
• Designs for both sides
Should not have
• Please do not just submit logo and a coloured card.
• It needs to have a design element to it
• No black background
• No clear cards - needs front & back

```html
<!DOCTYPE html>
<html lang="en">
<head>
<meta charset="utf-8">
<title>Larkspur Metrics – Business Card</title>
<link href="https://fonts.googleapis.com/css2?family=Open+Sans:wght@400;600;700&display=swap" rel="stylesheet">
<style>
  :root {
    --stage: #ececec;
    --orange: #f78f20;
    --orange-deep: #f26a21;
    --red-deep: #be1e2d;
    --brand-mark: #e0482a;
    --ink: #3d3d3d;
    --ink-soft: #5a5a5a;
    --rule: #2f3a3a;
    --paper: #ffffff;
    --ghost: #ededed;
  }
  * { box-sizing: border-box; margin: 0; padding: 0; }
  html, body { width: 1200px; height: 1000px; overflow: hidden; }
  body {
    background: var(--stage);
    font-family: "Open Sans", Arial, sans-serif;
    position: relative;
  }
  .card {
    position: absolute;
    width: 580px;
    height: 330px;
    border-radius: 26px;
    overflow: hidden;
    box-shadow: 0 10px 30px rgba(0,0,0,.18);
  }
  /* Front side */
  .card-front {
    left: 90px; top: 130px;
    background: linear-gradient(100deg, var(--orange-deep) 0%, #e4552a 45%, var(--red-deep) 100%);
    display: flex; align-items: center; justify-content: center;
  }
  .brand {
    display: flex; align-items: center; gap: 16px;
    font-weight: 600;
  }
  .brand-dot {
    border-radius: 50%;
    border: 3px solid currentColor;
    flex: none;
  }
  .card-front .brand { color: var(--paper); font-size: 34px; }
  .card-front .brand-dot { width: 64px; height: 64px; }

  /* Back side */
  .card-back {
    left: 530px; top: 520px;
    background: var(--paper);
  }
  .ghost-circle {
    position: absolute;
    left: -40px; top: 110px;
    width: 230px; height: 230px;
    border-radius: 50%;
    border: 10px solid var(--ghost);
  }
  .card-back .brand {
    position: absolute; right: 34px; top: 34px;
    color: var(--brand-mark); font-size: 20px; gap: 10px;
  }
  .card-back .brand-dot { width: 38px; height: 38px; border-width: 2px; }
  .address {
    position: absolute; right: 34px; top: 100px;
    text-align: right; font-size: 14px; color: var(--ink-soft); line-height: 1.45;
  }
  .holder { position: absolute; left: 40px; top: 150px; }
  .holder-name { font-size: 26px; font-weight: 700; letter-spacing: .3px; line-height: 1.1; }
  .holder-name .first { color: var(--red-deep); }
  .holder-name .last { color: var(--orange); }
  .holder-role { font-size: 15px; font-weight: 600; color: var(--ink-soft); margin-top: 2px; }
  .divider {
    position: absolute; left: 150px; right: 34px; top: 200px;
    height: 1.5px; background: var(--rule);
  }
  .contacts { position: absolute; left: 40px; top: 228px; list-style: none; }
  .contacts li {
    display: flex; align-items: center; gap: 12px;
    font-size: 15px; color: var(--ink); line-height: 26px;
  }
  .contacts svg { width: 13px; height: 13px; fill: var(--orange-deep); flex: none; }
  .contacts .accent { color: var(--orange-deep); }
</style>
</head>
<body>

  <section class="card card-front" aria-label="Card front">
    <div class="brand">
      <span class="brand-dot"></span>
      <span class="brand-name">Larkspur Metrics</span>
    </div>
  </section>

  <section class="card card-back" aria-label="Card back">
    <div class="ghost-circle" aria-hidden="true"></div>

    <div class="brand">
      <span class="brand-dot"></span>
      <span class="brand-name">Larkspur Metrics</span>
    </div>

    <p class="address">Your Street Address,<br>Singapore, 1234</p>

    <div class="holder">
      <h1 class="holder-name"><span class="first">DANA</span> <span class="last">WHITLOW</span></h1>
      <p class="holder-role">Ceo/Founer</p>
    </div>

    <div class="divider"></div>

    <ul class="contacts">
      <li>
        <svg viewBox="0 0 24 24"><path d="M6.6 10.8a15.1 15.1 0 0 0 6.6 6.6l2.2-2.2a1 1 0 0 1 1-.25 11.4 11.4 0 0 0 3.6.57 1 1 0 0 1 1 1V20a1 1 0 0 1-1 1A17 17 0 0 1 3 4a1 1 0 0 1 1-1h3.5a1 1 0 0 1 1 1c0 1.25.2 2.45.57 3.57a1 1 0 0 1-.25 1z"/></svg>
        +000 123 456 789
      </li>
      <li>
        <svg viewBox="0 0 24 24"><path d="M2 5h20v14H2z M2 5l10 8 10-8"/></svg>
        yourname@email.com
      </li>
      <li>
        <svg viewBox="0 0 24 24"><circle cx="12" cy="12" r="10"/></svg>
        <span>www.<span class="accent">websitename</span>.com</span>
      </li>
    </ul>
  </section>

</body>
</html>
```